Residential Mortgage Leader needs Wordpress Design

Looking for a home page website design for a client. We develop using the WordPress platform and would prefer the design be at least loosely based on an existing WordPress template. Attached files have many notes from our creative brief with client. The site must be responsive. Approved, basic wireframe attached. There is room for interpretation.

Existing web site: http://www.marisolkettering.example/

The Marisol Kettering Team relies on strong systems to deliver an on-time, done-right, friendly experience. Marisol offers mortgages and refinancing services throughout the United States. She is a successful Brookvale Funding agent who strives to be an active part of her community. She would like to focus the site on her team, rather than just her.

Difference makers...
When you work with the Marisol Kettering team you get a high level of expertise and a friendly experience.

She has amazing credentials. Marisol is widely recognized as a top producer for her company, and has earned a number of awards and honors for her customer service.

Marisol's team is very engaged and enjoys sharing social comments or photos from their community.

Imagery:
* Friendly, warm imagery, preferably of her team or an image to represent her team
* Clean and crisp
* Professional / Experts in mortgage and refinance
* Clean / Good use of white space
Updates

When possible, please use imagery from the DFW area. The client mentioned they would prefer not to see stock images. Thanks.

Amend that- creative use of stock images, however, is fine. A few designs have used stock imagery, but in a well-considered manner.

We added some photos and graphics that are local. We are Dallas / Ft. Worth, Plano, Frisco, Texas. We also added some examples of photos to use for the "In the Community" area. Stock photos of business folks just doesn't fit there. Thanks!

Target Market(s)

They service a lot of builders, but also work with homeowners. Their typical client is usually a woman searching for mortgage services online. She typically has a family and may refer her husband to Marisol's team. Keep in mind, however, they also see a number of other scenarios. Most of their clients are middle to high-end borrowers.

Industry/Entity Type

It Company

Requirements
Must have
• Design should be developed using program such as Photoshop or Fireworks or Illustrator as last preference. Ideally, the design would be based on an existing responsive WordPress theme, which we would customize. You must include the name of the target theme. The footer should include lots of space for disclaimers and legal language. Site navigation should include these choices: "Home, About, Builders, Mortgage Info, Approval, Blog, Contact"
Nice to have
• Blog, social media and photos area. Use of the already approved style prototype with colors and fonts (Lato- a Google font, Times New Roman and Cookie-a decorative Google font). However, we are open to interpretation.
Should not have
• Hard to read fonts or a lack of white space.

```html
<!DOCTYPE html>
<html lang="en">
<head>
<meta charset="utf-8">
<title>Brookvale Funding – Marisol Kettering Team</title>
<link href="https://fonts.googleapis.com/css2?family=Lato:wght@300;400;700&display=swap" rel="stylesheet">
<style>
:root{
  --red:#c4210f;
  --blue:#1f7fc0;
  --dark:#3a3a3a;
  --text:#444;
  --muted:#999;
  --light:#f1f1f1;
  --white:#fff;
  --foot-bar:#e1e3d2;
}
*{box-sizing:border-box;margin:0;padding:0}
html,body{width:710px;height:1200px;overflow:hidden}
body{position:relative;font-family:'Lato',sans-serif;color:var(--text);background:var(--light);-webkit-font-smoothing:antialiased}
.abs{position:absolute}

.hero{left:0;top:0;width:710px;height:368px;
  background:
    radial-gradient(ellipse 120px 90px at 690px 330px,rgba(235,240,248,.95),rgba(235,240,248,0) 100%),
    radial-gradient(ellipse 110px 130px at 330px 150px,rgba(238,196,160,.9),rgba(238,196,160,0) 100%),
    radial-gradient(ellipse 70px 90px at 210px 300px,rgba(200,200,205,.85),rgba(200,200,205,0) 100%),
    radial-gradient(ellipse 130px 150px at 120px 250px,rgba(120,80,50,.55),rgba(120,80,50,0) 100%),
    linear-gradient(180deg,rgba(30,80,200,.0) 0%,rgba(0,0,0,0) 100%),
    linear-gradient(95deg,#d8c59c 0%,#e7d7b0 18%,#c9ad7c 30%,#6f9ad8 46%,#2f73d3 62%,#1c5cc6 100%)}
.hero-top{left:0;top:0;width:59px;height:54px;background:#1846b8}
.hero-shade{left:0;top:368px;width:710px;height:14px;background:radial-gradient(ellipse 330px 8px at 355px 0,rgba(0,0,0,.18),rgba(0,0,0,0))}

.site-header{left:59px;top:0;width:592px;height:70px;background:var(--white)}
.brand{left:12px;top:20px;font-weight:700;font-size:18px;color:var(--red);line-height:1}
.brand-sub{left:12px;top:42px;font-size:8px;color:#555}
.main-nav{right:10px;top:46px;display:flex;gap:28px;font-size:8px;color:#555;list-style:none}
.main-nav li.active{color:var(--red)}
.search-btn{left:632px;top:0;width:19px;height:20px;background:#666}
.slide-arrow{top:212px;width:33px;height:32px}
.slide-arrow.prev{left:59px;background:rgba(90,90,90,.6)}
.slide-arrow.next{left:618px;background:rgba(20,70,150,.8)}

.intro-title{left:0;top:400px;width:710px;text-align:center;font-size:21px;color:var(--red);font-weight:400}
.intro-text{left:0;top:431px;width:710px;text-align:center;font-size:9px;font-weight:400;color:#333}
.intro-rule{left:59px;top:456px;width:592px;height:1px;background:#ddd}
.intro-bar{left:322px;top:453px;width:59px;height:3px;background:var(--blue)}

.photo{display:block}
.card{background:var(--white);border-bottom:2px solid var(--blue)}
.card h3{position:absolute;left:10px;font-size:11px;font-weight:400;color:var(--red)}
.card .tag{position:absolute;left:10px;font-size:8.5px;font-weight:300;color:#777}
.card p{position:absolute;left:10px;font-size:6.5px;font-weight:300;line-height:13.6px;color:#444}
.learn-more{position:absolute;right:0;bottom:0;width:78px;height:21px;background:var(--blue);color:#fff;font-size:7px;font-weight:300;line-height:21px;padding-left:12px}
.learn-more::after{content:"›";position:absolute;right:0;top:0;width:19px;text-align:center;border-left:1px solid rgba(255,255,255,.5);font-size:10px}

.tabs-panel{left:59px;top:798px;width:592px;height:152px;background:var(--white)}
.tab-label{top:7px;height:17px;color:#fff;font-size:10px;font-weight:400;text-align:center;line-height:17px}
.tab-blog{left:11px;width:188px;background:var(--red)}
.tab-social{left:203px;width:188px;background:var(--dark)}
.tab-community{left:395px;width:188px;background:var(--blue)}
.post-title{font-size:8.5px;font-weight:300;color:#333}
.post-ex{font-size:6.5px;font-weight:300;color:#aaa;line-height:9.5px}
.social-row{background:#f1f1f1;font-size:6.5px;font-weight:300;line-height:9.5px;color:#333}
.community-text{font-size:6.5px;font-weight:300;line-height:13.6px;color:#333}

.site-footer{left:0;top:978px;width:710px;height:172px;background:var(--dark);color:#999}
.footer-name{font-size:10.5px;font-weight:300;color:#eee;line-height:14px}
.footer-h{font-size:10.5px;font-weight:300;color:#eee}
.footer-list{list-style:none;font-size:6.5px;font-weight:300;line-height:15.8px}
.footer-about{font-size:6.5px;font-weight:300;line-height:15.8px}

.bottom-bar{left:0;top:1150px;width:710px;height:50px;background:var(--foot-bar)}
.bottom-brand{left:70px;top:15px;font-weight:700;font-size:11px;color:var(--red)}
.bottom-sub{left:70px;top:29px;font-size:5px;color:#555}
.social-btns{right:86px;top:14px;display:flex;gap:4px}
.social-btns span{width:14px;height:14px;background:#a9aba0;display:block}
</style>
</head>
<body>
<div class="abs hero" role="img" aria-label="Photo of a hand holding house keys in front of a cream two-storey home under a blue sky"></div>
<div class="abs hero-top"></div>
<div class="abs hero-shade"></div>

<header class="abs site-header">
  <div class="abs brand">Brookvale Funding</div>
  <div class="abs brand-sub">A Harrowgate Capital Company</div>
  <ul class="abs main-nav">
    <li class="active">Home</li><li>About</li><li>Builders</li><li>Mortage Info</li><li>Approval Blog</li><li>Contact Info</li>
  </ul>
</header>
<div class="abs search-btn"><svg width="19" height="20"><circle cx="9" cy="9" r="2.5" fill="none" stroke="#ddd" stroke-width="1"/><line x1="11" y1="11" x2="13" y2="13" stroke="#ddd"/></svg></div>
<div class="abs slide-arrow prev"><svg width="33" height="32"><polyline points="19,10 13,16 19,22" fill="none" stroke="#999" stroke-width="2"/></svg></div>
<div class="abs slide-arrow next"><svg width="33" height="32"><polyline points="14,10 20,16 14,22" fill="none" stroke="#5b8fd8" stroke-width="2"/></svg></div>

<h1 class="abs intro-title">EARNING YOUR BUSINESS</h1>
<p class="abs intro-text">The Marisol Kettering Team relies on strong systems to deliver an on-time, done-right and friendly experience.</p>
<div class="abs intro-rule"></div>
<div class="abs intro-bar"></div>

<div class="abs photo" style="left:59px;top:489px;width:154px;height:277px;background:
  radial-gradient(ellipse 60px 40px at 70px 150px,rgba(230,225,205,.8),rgba(230,225,205,0)),
  linear-gradient(180deg,#a9c6dc 0%,#5d8a5a 18%,#3d6a3c 35%,#2f5d48 45%,#8a7a5c 58%,#3f7040 70%,#43c6e6 80%,#8fe0f0 100%)" role="img" aria-label="Photo of a tropical house among palm trees with a swimming pool"></div>
<section class="abs card" style="left:213px;top:489px;width:147px;height:277px">
  <h3 style="top:50px">OUR CREDENTIALS</h3>
  <div class="tag" style="top:69px">A top-producer, top-notch</div>
  <p style="top:94px;width:130px">Lorem Ipsum is simply dummy text of the printing and typesetting industry. Lorem Ipsum has been the industry's standard dummy text ever since the 1500s, when an unknown printer took a galley of type and scrambled it to make a type specimen book. It has survived not only five centuries, but also the leap into.</p>
  <div class="learn-more">Learn more</div>
</section>
<div class="abs photo" style="left:360px;top:489px;width:154px;height:139px;background:
  radial-gradient(ellipse 50px 60px at 80px 55px,#f3d56a 0%,#c89a2c 45%,rgba(120,90,30,0) 100%),
  linear-gradient(180deg,#6b5a2e 0%,#243e58 60%,#1a2c40 100%)" role="img" aria-label="Photo of a gold trophy cup"></div>
<section class="abs card" style="left:514px;top:489px;width:137px;height:139px">
  <h3 style="top:16px">AWARDS</h3>
  <div class="tag" style="top:35px">A top-producer, top-notch</div>
  <p style="top:59px;width:120px">Lorem Ipsum is simply dummy text of the printing and typesetting industry.</p>
  <div class="learn-more">Learn more</div>
</section>
<div class="abs photo" style="left:360px;top:628px;width:154px;height:138px;background:
  radial-gradient(ellipse 40px 60px at 70px 70px,rgba(210,215,215,.85),rgba(210,215,215,0)),
  radial-gradient(ellipse 30px 70px at 140px 80px,rgba(120,30,30,.9),rgba(120,30,30,0)),
  linear-gradient(90deg,#161a1a 0%,#4a504e 40%,#3c3e3a 70%,#2e6a3a 100%)" role="img" aria-label="Photo of a person pressing a hand against a glass scan panel"></div>
<section class="abs card" style="left:514px;top:628px;width:137px;height:138px">
  <h3 style="top:15px">RECOGNION</h3>
  <div class="tag" style="top:34px">A top-producer, top-notch</div>
  <p style="top:58px;width:120px">Lorem Ipsum is simply dummy text of the printing and typesetting industry.</p>
  <div class="learn-more">Learn more</div>
</section>

<section class="abs tabs-panel">
  <div class="abs tab-label tab-blog">BLOG</div>
  <div class="abs tab-label tab-social">SOCIALS</div>
  <div class="abs tab-label tab-community">IN THE COMMUNITY</div>

  <div class="abs" style="left:12px;top:36px;width:46px;height:45px;background:linear-gradient(180deg,#5a2e14 0%,#8a4a22 40%,#e8dcc0 70%,#c9a77a 100%)" role="img" aria-label="Photo of an open book on a shelf"></div>
  <div class="abs post-title" style="left:67px;top:42px">Borrwoing</div>
  <div class="abs post-ex" style="left:67px;top:56px;width:105px">Lorem Ipsum is simply dummy text of the and typesetting.</div>
  <div class="abs" style="left:12px;top:94px;width:46px;height:45px;background:linear-gradient(180deg,#5a2e14 0%,#8a4a22 40%,#e8dcc0 70%,#c9a77a 100%)" role="img" aria-label="Photo of an open book on a shelf"></div>
  <div class="abs post-title" style="left:67px;top:100px">Best Practice</div>
  <div class="abs post-ex" style="left:67px;top:114px;width:105px">Lorem Ipsum is simply dummy text of the and typesetting.</div>
  <div class="abs" style="left:196px;top:37px;width:1px;height:100px;background:#ccc"></div>
  <div class="abs" style="left:195px;top:45px;width:3px;height:16px;background:var(--red)"></div>

  <div class="abs social-row" style="left:204px;top:36px;width:186px;height:46px">
    <div class="abs" style="left:0;top:0;width:46px;height:46px;background:linear-gradient(135deg,#f4ece2 0%,#dcb894 50%,#b07a52 100%)" role="img" aria-label="Photo of a smiling couple"></div>
    <div class="abs" style="left:55px;top:13px;width:120px">Lorem Ipsum is simply dummy text of the and typesetting. industry.</div>
  </div>
  <div class="abs social-row" style="left:204px;top:93px;width:186px;height:46px">
    <div class="abs" style="left:0;top:0;width:46px;height:46px;background:linear-gradient(135deg,#e4eef6 0%,#8aa8c8 45%,#26406a 100%)" role="img" aria-label="Photo of business people shaking hands"></div>
    <div class="abs" style="left:55px;top:13px;width:120px">Lorem Ipsum is simply dummy text of the and typesetting. industry.</div>
  </div>

  <p class="abs community-text" style="left:396px;top:37px;width:96px">Lorem Ipsum is simply dummy text of the printing and typesetting industry. Lorem Ipsum has been the industry's standard dummy text ever since the 1500s, when an unknown.</p>
  <div class="abs" style="left:494px;top:35px;width:88px;height:104px;background:linear-gradient(110deg,#4a3a2c 0%,#d8b88c 35%,#8a6a4a 50%,#2d4e7a 70%,#7aa0cc 100%)" role="img" aria-label="Photo of a curved office building facade"></div>
</section>

<footer class="abs site-footer">
  <div class="abs" style="left:70px;top:20px;width:108px;height:127px;background:
    radial-gradient(ellipse 34px 44px at 54px 55px,rgba(222,180,150,.9),rgba(222,180,150,0)),
    linear-gradient(180deg,#2a2724 0%,#4e3626 55%,#2e2622 100%)" role="img" aria-label="Portrait photo of Marisol Kettering"></div>
  <div class="abs footer-name" style="left:190px;top:20px">Marisol Kettering,<br>Branch Manager</div>
  <ul class="abs footer-list" style="left:190px;top:53px">
    <li>Office: 555.204.7731</li><li>Cell: 555.318.4402</li><li>mkettering@brookvale.example</li><li>NMLS: 40219</li><li>4820 Larkspur Square, Ste. 210</li><li>Alder Springs, TX 75990</li>
  </ul>
  <div class="abs footer-h" style="left:344px;top:21px">Quick Link</div>
  <ul class="abs footer-list" style="left:344px;top:53px">
    <li>Home</li><li>About</li><li>Builders</li><li>Mortgage Info</li><li>Approval Blogs</li><li>Contact us</li>
  </ul>
  <div class="abs footer-h" style="left:457px;top:21px">About Us</div>
  <p class="abs footer-about" style="left:457px;top:53px;width:185px">Lorem Ipsum is simply dummy text of the printing and typesetting industry. Lorem Ipsum has been the industry's standard dummy text ever since the 1500s, when an unknown printer took a galley of type and scrambled it to make a type specimen book. It has survived not only five centuries.</p>
</footer>

<div class="abs bottom-bar">
  <div class="abs bottom-brand">Brookvale Funding</div>
  <div class="abs bottom-sub">A Harrowgate Capital Company</div>
  <div class="abs social-btns"><span></span><span></span><span></span><span></span><span></span></div>
</div>
</body>
</html>
```